Business Cards - Brightpath Horizon

need to design unique business card for my mortgage business. I need to design credit card style business card for my business or any unique idea that you might have

Target Market(s)

Home Loan customers

Industry/Entity Type

Mortgage Brokerage

Contact Information for Business Card

please design credit card style or very unique style business card

Colors

Designer to choose colors to be used in the design.

Requirements
Must have
• Name
• position
• Phone number
• fax number
• email address
• website address
• social media address
• All above fields will be provided once design in finalised

```html
<!DOCTYPE html>
<html lang="en">
<head>
<meta charset="utf-8">
<title>Brightpath Horizon – Business Card</title>
<link rel="stylesheet" href="https://fonts.googleapis.com/css2?family=Marcellus&family=Lora:ital@1&family=Work+Sans:wght@400;500&display=swap">
<style>
  :root {
    --navy: #3d4a8c;
    --orange: #e27f24;
    --teal: #2fa3a8;
    --ink: #4e5566;
    --card: #f3f1ee;
    --backdrop: #e6e2dc;
  }
  html, body {
    margin: 0;
    padding: 0;
    width: 1200px;
    height: 1047px;
    overflow: hidden;
    background: var(--backdrop);
  }
  .card {
    position: absolute;
    left: 80px;
    top: 240px;
    width: 1040px;
    height: 568px;
    background: var(--card);
    border: 1px solid #d9d4cc;
    border-radius: 26px;
    overflow: hidden;
    box-shadow: 0 6px 24px rgba(0,0,0,0.08);
  }
  .brand {
    position: absolute;
    left: 90px;
    top: 112px;
    width: 460px;
  }
  .brand-name {
    margin: 0;
    font-family: "Marcellus", serif;
    font-weight: 400;
    color: var(--navy);
    font-size: 54px;
    line-height: 1.02;
    letter-spacing: 1px;
    text-transform: uppercase;
  }
  .brand-tagline {
    margin: 18px 0 0;
    font-family: "Lora", serif;
    font-style: italic;
    color: var(--orange);
    font-size: 25px;
  }
  .person {
    position: absolute;
    left: 618px;
    top: 50px;
    right: 0;
  }
  .person-name {
    margin: 0;
    font-family: "Marcellus", serif;
    color: var(--navy);
    font-size: 36px;
    letter-spacing: 1px;
    font-weight: 400;
  }
  .person-role {
    margin: 2px 0 0;
    font-family: "Work Sans", sans-serif;
    color: var(--orange);
    font-size: 20px;
    letter-spacing: 0.5px;
  }
  .divider {
    height: 2px;
    background: var(--navy);
    margin-top: 12px;
  }
  .contact {
    list-style: none;
    margin: 14px 0 0;
    padding: 0;
    font-family: "Work Sans", sans-serif;
    color: var(--ink);
    font-size: 21px;
    line-height: 27px;
  }
  .contact li {
    display: flex;
    align-items: center;
  }
  .contact .icon {
    width: 12px;
    height: 12px;
    margin-right: 17px;
    flex: none;
  }
  .skyline {
    position: absolute;
    left: 0;
    right: 0;
    bottom: 0;
    height: 170px;
    background: linear-gradient(90deg, var(--navy) 0%, var(--navy) 40%, var(--teal) 55%, var(--navy) 68%, var(--orange) 82%, var(--orange) 100%);
    opacity: 0.9;
  }
</style>
</head>
<body>
  <div class="card">
    <div class="brand">
      <p class="brand-name">Brightpath<br>Horizon</p>
      <p class="brand-tagline">Your path home, made bright</p>
    </div>

    <div class="person">
      <h1 class="person-name">DANIEL HART</h1>
      <p class="person-role">Founder</p>
      <div class="divider"></div>
      <ul class="contact">
        <li>480 Harbor View Ave.</li>
        <li>Coral Bay, FL 33012</li>
        <li>
          <svg class="icon" viewBox="0 0 12 12" aria-hidden="true"><path d="M2.5 1 L4.5 1 L5.2 3.6 L4 4.6 C4.6 6 5.9 7.4 7.4 8 L8.4 6.8 L11 7.5 L11 9.5 C11 10.3 10.3 11 9.5 11 C5 11 1 7 1 2.5 C1 1.7 1.7 1 2.5 1 Z" fill="#e27f24"/></svg>
          555-014-2837
        </li>
        <li>
          <svg class="icon" viewBox="0 0 12 12" aria-hidden="true"><rect x="3" y="1" width="6" height="3.5" fill="none" stroke="#e27f24" stroke-width="1.2"/><rect x="1" y="4.5" width="10" height="4.5" fill="#e27f24"/><rect x="3" y="8" width="6" height="3" fill="#fff" stroke="#e27f24" stroke-width="1.2"/></svg>
          Fax 555-014-2838
        </li>
        <li>
          <svg class="icon" viewBox="0 0 12 12" aria-hidden="true"><rect x="1" y="2.5" width="10" height="7" fill="none" stroke="#e27f24" stroke-width="1.3"/><path d="M1 2.5 L6 6.5 L11 2.5" fill="none" stroke="#e27f24" stroke-width="1.3"/></svg>
          hello@brightpathhorizon.com
        </li>
        <li>
          <svg class="icon" viewBox="0 0 12 12" aria-hidden="true"><circle cx="6" cy="6" r="5" fill="none" stroke="#e27f24" stroke-width="1.2"/><ellipse cx="6" cy="6" rx="2.2" ry="5" fill="none" stroke="#e27f24" stroke-width="1"/><path d="M1 6 H11" stroke="#e27f24" stroke-width="1"/></svg>
          www.BrightpathHorizon.com
        </li>
        <li>
          <svg class="icon" viewBox="0 0 12 12" aria-hidden="true"><circle cx="9" cy="2.5" r="1.8" fill="#e27f24"/><circle cx="3" cy="6" r="1.8" fill="#e27f24"/><circle cx="9" cy="9.5" r="1.8" fill="#e27f24"/><path d="M9 2.5 L3 6 L9 9.5" fill="none" stroke="#e27f24" stroke-width="1"/></svg>
          @brightpathhorizon
        </li>
      </ul>
    </div>

    <div class="skyline" role="img" aria-label="Decorative band of house rooftops in navy, teal and orange"></div>
  </div>
</body>
</html>
```